Website design for legal tech start up in Switzerland (B2B)

We are for a legal tech start up in Switzerland called KOVA. We have been running since August 2016. This will be our first live website.

We need a website designed and business card design for our start-up in Switzerland. We also need the Web design to be converted into HTML and CSS files.

Function of website:
• To inform potential customers of our services
• Form a key part of our digital marketing and sales footprint.
• Branding

Please find attached logo.
Updates

Project Deadline Extended Reason: Giving us time to review submissions and provide opportunity for more submissions. Added Thursday, February 16, 2017

Project Deadline Extended
Reason: Looking for more idea's not necessarily set on blue and grey colours only.

Target Market(s)

B2B tech powered legal services.

Industry/Entity Type

Legal

Contact Information for Business Card

Lean and slick design.

Coding

Coded - Design and coding required

Number of Pages Required

5+ page

Requirements
Must have
• VERY LEAN AND CLEAN DESIGN!
• We have received many great standard designs, but we are looking for something more out-of-the box: You can get inspiration from these designs: http://www.pixelvane.com/websites/clean/
• Thanks!!
• Easy content management system
• Well structured coding for additional development
• Responsive webpage for all types of devices
• SEO optimized
• Tabs (Home, services, team, careers, blog, contact us)
• Colour scheme complementary to logo
Nice to have
• Look and Design - Approachable, High-tech, Modern
• Easy to add chat bot capability in future
Should not have
• Too busy/ too much clutter
• Not take to long to load

```html
<!DOCTYPE html>
<html lang="en">
<head>
<meta charset="utf-8">
<title>KOVA – Legal Tech</title>
<link href="https://fonts.googleapis.com/css2?family=Raleway:wght@400;500;600;800&family=Open+Sans:wght@400;600&display=swap" rel="stylesheet">
<style>
:root{
  --navy:#1c3d6e;
  --blue:#2a73b8;
  --ink:#333a40;
  --text:#555;
  --muted:#777;
  --charcoal:#474747;
  --btn-grey:#6b6b6b;
  --line:#cfcfcf;
  --white:#fff;
}
*{margin:0;padding:0;box-sizing:border-box}
html,body{width:1200px;height:2500px;overflow:hidden;background:var(--white)}
body{position:relative;font-family:"Open Sans",Arial,sans-serif;color:var(--text)}
.abs{position:absolute}

/* header */
.site-header{left:0;top:0;width:1200px;height:88px;background:var(--white)}
.brand{font-family:"Raleway",Arial,sans-serif;font-weight:800;color:var(--ink);letter-spacing:2px;line-height:1}
.site-header .brand{left:150px;top:20px;font-size:48px}
.main-nav{right:170px;top:30px;display:flex;gap:22px;align-items:center}
.main-nav a{font-family:"Raleway",Arial,sans-serif;font-size:15px;color:#8a8a8a;text-decoration:none;letter-spacing:.5px;padding:5px 8px}
.main-nav a.active{color:var(--navy);border:2px solid var(--navy);padding:4px 22px;font-weight:600}

/* hero */
.hero{left:0;top:88px;width:1200px;height:532px;
  background:linear-gradient(180deg,#8aa6c4 0%,#dfe6ee 22%,#b7c3cf 38%,#4d7a3c 55%,#6d8a4a 70%,#5a6a55 88%,#7a8a95 100%)}
.hero-caption{left:120px;top:315px;width:485px;height:115px;background:rgba(40,60,90,.55);padding:18px 28px}
.hero-caption h1{font-family:"Raleway",Arial,sans-serif;font-weight:600;color:var(--white);font-size:31px;line-height:1.25;text-transform:uppercase;letter-spacing:.5px}
.hero-caption h1 span{font-size:26px}
.slider-dots{left:556px;top:558px;display:flex;gap:9px}
.slider-dots i{width:13px;height:13px;border-radius:50%;background:var(--white);display:block}
.slider-dots i.off{background:transparent;border:2px solid var(--white)}

/* feature boxes */
.feature{top:597px;width:452px;height:246px;padding:55px 42px;color:var(--white)}
.feature.why{left:145px;background:var(--charcoal)}
.feature.services{left:597px;background:var(--navy)}
.feature h2{font-family:"Raleway",Arial,sans-serif;font-weight:500;font-size:21px;margin-bottom:8px}
.feature p{font-size:12.5px;line-height:1.55;width:270px;color:#e2e2e2}
.feature .btn{display:inline-block;margin-top:18px;width:125px;height:32px;line-height:32px;text-align:center;font-size:11px;color:var(--white);text-transform:uppercase}
.why .btn{background:var(--btn-grey)}
.services .btn{background:#2e5690}
.feature svg{position:absolute;right:45px;top:63px}

/* about */
.about{left:0;top:893px;width:1200px;height:422px;
  background:linear-gradient(120deg,#e4e4e4 0%,#efefef 40%,#e8e8e8 70%,#dcdcdc 100%);text-align:center}
.about h2{font-family:"Raleway",Arial,sans-serif;font-weight:500;font-size:36px;color:var(--ink);margin-top:70px;letter-spacing:1px}
.about h2 span{color:var(--navy)}
.about .lead{font-size:18.5px;line-height:1.6;color:var(--muted);width:700px;margin:16px auto 0}
.about .body{font-size:16px;line-height:1.8;color:var(--muted);width:730px;margin:18px auto 0}
.btn-outline{display:inline-block;margin-top:36px;width:130px;height:34px;line-height:30px;border:2px solid var(--navy);color:var(--navy);font-size:13px;text-transform:uppercase;background:var(--white)}

/* blogs */
.section-title{font-family:"Raleway",Arial,sans-serif;font-weight:500;font-size:28px;color:var(--blue);letter-spacing:.5px}
.blogs-title{left:143px;top:1368px}
.blog-card{top:1423px;width:285px}
.blog-card .thumb{height:153px}
.blog-card h3{font-family:"Open Sans",Arial,sans-serif;font-weight:400;font-size:16.5px;color:#222;margin:12px 3px 6px}
.blog-card p{font-size:11.5px;line-height:1.65;color:var(--muted);margin:0 3px;padding-bottom:14px;border-bottom:1.5px solid var(--line);width:272px}
.blog-card a{display:block;margin:12px 3px;font-size:13px;color:var(--navy);text-decoration:none;text-transform:uppercase}

.divider{left:0;top:1797px;width:1200px;height:2px;background:#d8d8d8}

/* team */
.team-title{left:0;top:1830px;width:1200px;text-align:center}
.member{top:1890px;width:226px;text-align:center}
.member .portrait{width:158px;height:158px;border-radius:50%;margin:0 auto;border:2px solid #ccc}
.member h4{font-family:"Open Sans",Arial,sans-serif;font-weight:400;font-size:17px;color:var(--navy);margin-top:14px}
.member p{font-size:12.5px;line-height:1.5;color:var(--text);margin-top:2px}

/* footer */
.site-footer{left:0;top:2175px;width:1200px;height:270px;
  background:linear-gradient(160deg,#dfe7ee 0%,#eef2f6 35%,#d3dde6 70%,#e8edf2 100%)}
.site-footer .brand{left:175px;top:63px;font-size:48px}
.footer-col{top:50px}
.footer-col h5{font-family:"Raleway",Arial,sans-serif;font-weight:500;font-size:16px;color:var(--ink);letter-spacing:.5px;margin-bottom:12px}
.footer-col li{list-style:none;font-size:12px;color:#333;line-height:30px}
.social{display:flex;gap:5px}
.social i{display:block;width:30px;height:30px;border:1.5px solid #222;border-radius:50%}
.copyright{left:0;top:2462px;width:1150px;text-align:center;font-size:11.5px;color:#666}
</style>
</head>
<body>

<header class="site-header abs">
  <div class="brand abs">KOVA</div>
  <nav class="main-nav abs">
    <a class="active" href="#">HOME</a>
    <a href="#">SERVICES</a>
    <a href="#">TEAM</a>
    <a href="#">CAREERS</a>
    <a href="#">BLOG</a>
    <a href="#">CONTACT US</a>
  </nav>
</header>

<section class="hero abs" role="img" aria-label="Swiss lakeside village with a church tower, green trees and snow-capped mountains"></section>
<div class="hero-caption abs">
  <h1>Vestibulum ligula<br><span>Augue bibendum accumsan</span></h1>
</div>
<div class="slider-dots abs"><i class="off"></i><i></i><i></i><i></i></div>

<article class="feature why abs">
  <h2>WHY WE ARE</h2>
  <p>Praesent elementum elit at tellus Curabitur metus ipsum luctus eu malesuada ut tincidunt sed diam Donec quis mi sed</p>
  <span class="btn">Learn more</span>
  <svg width="115" height="100" viewBox="0 0 115 100" fill="none" stroke="#fff" stroke-width="3.5">
    <rect x="4" y="22" width="107" height="72" rx="6"/>
    <path d="M40 22V10a5 5 0 0 1 5-5h25a5 5 0 0 1 5 5v12"/>
    <path d="M4 50h45M66 50h45"/>
    <rect x="49" y="43" width="17" height="14" rx="2"/>
  </svg>
</article>

<article class="feature services abs">
  <h2>OUR SERVICES</h2>
  <p>Praesent elementum elit at tellus Curabitur metus ipsum luctus eu malesuada ut tincidunt sed diam Donec quis mi sed magna</p>
  <span class="btn">Learn more</span>
  <svg width="90" height="125" viewBox="0 0 90 125" fill="none" stroke="#fff" stroke-width="3.5">
    <path d="M8 18h52l24 24v78H8z"/>
    <path d="M60 18v24h24"/>
    <path d="M22 60h48M22 72h48M22 84h48M22 96h48"/>
    <path d="M26 30V8a6 6 0 0 1 12 0v28a3 3 0 0 1-6 0V14"/>
  </svg>
</article>

<section class="about abs" role="img" aria-label="Soft faded photo of a person in a white shirt writing at a desk">
  <h2>ABOUT <span>KOVA</span></h2>
  <p class="lead">Praesent elementum elit at tellus Curabitur metus ipsum luctus eu malesuada ut tincidunt sed diam Donec quis mi sed magna hendrerit accumsan</p>
  <p class="body">Curabitur iaculis tempus eros Curabitur vel mi sit amet magna malesuada ultrices Ut nisi erat fermentum vel congue id euismod in elit Fusce ultricies orci ac feugiat suscipit leo massa sodales velit et scelerisque mi tortor at ipsum Proin orci</p>
  <span class="btn-outline">Learn more</span>
</section>

<h2 class="section-title blogs-title abs">OUR BLOGS</h2>

<article class="blog-card abs" style="left:145px">
  <div class="thumb" role="img" aria-label="Business people signing a document at a desk" style="background:linear-gradient(135deg,#dfe6ec,#a8b6c2 55%,#2d2f33)"></div>
  <h3>Donec scelerisque leo ac risus</h3>
  <p>Praesent elementum elit at tellus Curabitur metus ipsum luctus eu malesuada ut tincidunt sed diam Donec quis mi sed magna hendrerit</p>
  <a href="#">Learn more</a>
</article>
<article class="blog-card abs" style="left:458px">
  <div class="thumb" role="img" aria-label="Team meeting around a white conference table" style="background:linear-gradient(135deg,#5a6068,#c8ccd2 50%,#eceff2)"></div>
  <h3>Donec scelerisque leo ac risus</h3>
  <p>Praesent elementum elit at tellus Curabitur metus ipsum luctus eu malesuada ut tincidunt sed diam Donec quis mi sed magna hendrerit</p>
  <a href="#">Learn more</a>
</article>
<article class="blog-card abs" style="left:772px">
  <div class="thumb" role="img" aria-label="Colleagues discussing work over a laptop" style="background:linear-gradient(135deg,#c98f78,#e7d3c8 50%,#b86a5c)"></div>
  <h3>Donec scelerisque leo ac risus</h3>
  <p>Praesent elementum elit at tellus Curabitur metus ipsum luctus eu malesuada ut tincidunt sed diam Donec quis mi sed magna hendrerit</p>
  <a href="#">Learn more</a>
</article>

<div class="divider abs"></div>

<h2 class="section-title team-title abs">OUR TEAM</h2>

<div class="member abs" style="left:147px">
  <div class="portrait" role="img" aria-label="Team member portrait" style="background:linear-gradient(180deg,#e4e6e8,#c9ccd0)"></div>
  <h4>Member Name</h4>
  <p>Proin nulla arcu nonummy luctus dictum eget fermentum et</p>
</div>
<div class="member abs" style="left:374px">
  <div class="portrait" role="img" aria-label="Team member portrait" style="background:linear-gradient(180deg,#4fa3a8,#8f7fb0)"></div>
  <h4>Member Name</h4>
  <p>Proin nulla arcu nonummy luctus dictum eget fermentum et</p>
</div>
<div class="member abs" style="left:600px">
  <div class="portrait" role="img" aria-label="Team member portrait" style="background:linear-gradient(180deg,#e2e2e2,#3b3e44)"></div>
  <h4>Member Name</h4>
  <p>Proin nulla arcu nonummy luctus dictum eget fermentum et</p>
</div>
<div class="member abs" style="left:827px">
  <div class="portrait" role="img" aria-label="Team member portrait" style="background:linear-gradient(180deg,#dfe8ef,#7fa4c8)"></div>
  <h4>Member Name</h4>
  <p>Proin nulla arcu nonummy luctus dictum eget fermentum et</p>
</div>

<footer class="site-footer abs" role="img" aria-label="Pale snowy mountain landscape">
  <div class="brand abs">KOVA</div>
  <div class="footer-col abs" style="left:402px">
    <h5>COMPANY</h5>
    <ul><li>Home</li><li>What We Offer</li><li>Our Services</li><li>Career</li></ul>
  </div>
  <div class="footer-col abs" style="left:572px">
    <h5>SUBLINKS</h5>
    <ul><li>Our Services</li><li>Team</li><li>Our Blogs</li></ul>
  </div>
  <div class="footer-col abs" style="left:740px">
    <h5>RESOURCE</h5>
    <ul><li>Privacy Policy</li><li>FAQ</li><li>Contact Us</li></ul>
  </div>
  <div class="footer-col abs" style="left:918px">
    <h5>FOLLOW US</h5>
    <div class="social"><i></i><i></i><i></i><i></i></div>
  </div>
</footer>

<p class="copyright abs">© 2017 Company Name &nbsp;All right reserved &nbsp;Term of Use</p>

</body>
</html>
```